NZ First of it's kind solutions directory and marketplace for busy Mums needs a business card design

We need a business card design for our new nationwide business in NZ (long term plans to go global). We provide solutions to the everyday challenges that busy Mums face by connecting them with quality communities and suppliers of carefully selected, relevant products and services. We sell direct via our online marketplace. The final design should communicate our values of inclusivity, quality and smart solutions. Colours should incorporate our logo colour palette of #477077 and #6ba8b2. Our website is at https://www.brightnestmums.example

Target Market(s)

busy Mums, Age 28 – 50, female, income over $100K, location main centres NZ primarily but NZ wide. Is likely juggling work or career with a young family. Probably had hobbies which have fallen by the wayside.
-Wants to succeed in her chosen career without compromising on family life
-to successfully juggle her career without feeling like she is compromising her children
- Is time poor, something always has to give and it’s generally her health (she’ll stay up late, get stressed)
- probably ex corporate or professional career. Has discretional income

Industry/Entity Type

Business

Contact Information for Business Card

Lena Forbisher, Founder, BrightNestMums.example (Strapline Tap; Gather; Sorted), 47 Kowhai Terrace, Ellerslie, Auckland 1051, New Zealand. Mob: 021 483 517 Ph: +64 (0)9 571 4860

Font styles to use
Other font styles liked:
• Raleway, and/or Architects Daughter

Colors
00a990
33b8a4
86cfc6
cfeae6

Requirements
Must have
• the above details, streamline. the logo and colours associated with those logos
Should not have
• foil or metallic colours

```html
<!DOCTYPE html>
<html lang="en">
<head>
<meta charset="utf-8">
<title>BrightNestMums — Business Card</title>
<link href="https://fonts.googleapis.com/css2?family=Roboto:wght@400;500&family=Roboto+Condensed:wght@400;500&display=swap" rel="stylesheet">
<style>
  :root {
    --backdrop: #2a2a2a;
    --paper: #f1f1f1;
    --teal-deep: #477077;
    --teal-light: #6ba8b2;
    --white: #ffffff;
  }
  html, body {
    margin: 0;
    padding: 0;
    width: 1200px;
    height: 960px;
    overflow: hidden;
    background: var(--backdrop);
  }
  .canvas {
    position: relative;
    width: 1200px;
    height: 960px;
  }
  .card {
    position: absolute;
    width: 600px;
    height: 342px;
    overflow: hidden;
  }
  /* Front */
  .card-front {
    left: 314px;
    top: 113px;
    background: var(--paper);
  }
  .brand {
    position: absolute;
    left: 0;
    top: 0;
    width: 600px;
    height: 208px;
    display: flex;
    align-items: center;
    justify-content: center;
    gap: 14px;
  }
  .brand-dot {
    width: 40px;
    height: 40px;
    border-radius: 50%;
    background: var(--teal-deep);
  }
  .brand-name {
    font-family: "Roboto", Arial, sans-serif;
    font-weight: 500;
    font-size: 40px;
    letter-spacing: -0.5px;
    color: var(--teal-deep);
  }
  .identity {
    position: absolute;
    left: 0;
    top: 210px;
    width: 286px;
    height: 132px;
    background: var(--teal-deep);
    color: var(--white);
    text-align: center;
  }
  .identity-name {
    margin: 42px 0 0;
    font-family: "Roboto Condensed", Arial, sans-serif;
    font-weight: 500;
    font-size: 24px;
    line-height: 26px;
  }
  .identity-role {
    margin: 2px 0 0;
    font-family: "Roboto", Arial, sans-serif;
    font-size: 16px;
    letter-spacing: 0.5px;
  }
  .contact {
    position: absolute;
    left: 288px;
    top: 210px;
    width: 312px;
    height: 132px;
    background: var(--teal-light);
    color: var(--white);
    font-family: "Roboto", Arial, sans-serif;
    font-size: 14.5px;
    line-height: 19px;
    text-align: right;
    box-sizing: border-box;
    padding: 20px 37px 0 0;
  }
  .contact p { margin: 0; }
  .contact .address { margin-top: 5px; }
  /* Back */
  .card-back {
    left: 311px;
    top: 472px;
    background: var(--teal-light);
    color: var(--white);
    text-align: center;
  }
  .back-mark {
    position: absolute;
    left: 0;
    top: 70px;
    width: 600px;
    display: flex;
    flex-direction: column;
    align-items: center;
    gap: 18px;
  }
  .back-dot {
    width: 120px;
    height: 120px;
    border-radius: 50%;
    background: var(--white);
  }
  .back-name {
    font-family: "Roboto", Arial, sans-serif;
    font-weight: 500;
    font-size: 30px;
    color: var(--white);
  }
  .strapline {
    position: absolute;
    left: 0;
    top: 304px;
    width: 600px;
    margin: 0;
    font-family: "Roboto", Arial, sans-serif;
    font-size: 14.5px;
  }
</style>
</head>
<body>
<main class="canvas">
  <section class="card card-front" aria-label="Business card front">
    <div class="brand">
      <span class="brand-dot" aria-hidden="true"></span>
      <span class="brand-name">BrightNestMums</span>
    </div>
    <div class="identity">
      <p class="identity-name">LENA FORBISHER</p>
      <p class="identity-role">FOUNDER</p>
    </div>
    <div class="contact">
      <p>(P)+64 (0)9 571 4860</p>
      <p>(M) 021 483 517</p>
      <p>www.BrightNestMums.example</p>
      <p class="address">47 Kowhai Terrace, Ellerslie</p>
      <p>Auckland 1051, New Zealand</p>
    </div>
  </section>

  <section class="card card-back" aria-label="Business card back">
    <div class="back-mark">
      <span class="back-dot" aria-hidden="true"></span>
      <span class="back-name">BrightNestMums</span>
    </div>
    <p class="strapline">Tap; Gather; Sorted</p>
  </section>
</main>
</body>
</html>
```